Building company buisness cards

We are looking for a sharp modern new look for our business cards.
We are a New Zealand based company that specialises in house and land packages.
We have attached a photo of the current logo and would like to see if it can be improved somehow if needed.
We are open to any colours but we have chosen green at this stage.
Feel free to change the font and make the logo smarter looking.
Play with the colours and see what looks best.

We want a card that looks so good know one will want to throw it away!

Target Market(s)

Home buyers

Industry/Entity Type

Building

Contact Information for Business Card

Derek Tolvane
0217394062
dtolvane@quillmarkhomesteads.co.nz
quillmarkhomesteads.co.nz

Font styles to use
Serif
Sans Serif

Colors

Designer to choose colors to be used in the design.

Requirements
Must have
• Logo and company name on one side, details on the other side
Nice to have
• Color codes for the original green are HEX #4a8028, RGB(74,128,40), CMYK(42,0,69,50)
• Round corners, Raised and/or spot UV

```html
<!DOCTYPE html>
<html lang="en">
<head>
<meta charset="utf-8">
<title>Quillmark Homesteads – Business Cards</title>
<link rel="stylesheet" href="https://fonts.googleapis.com/css2?family=Montserrat:wght@700&family=Roboto:wght@400&display=swap">
<style>
  :root {
    --brand-green: #4a8028;
    --paper: #ffffff;
    --ink-grey: #5a5a5a;
    --rule-grey: #7a7a7a;
    --backdrop: #9c9c9c;
  }
  * { box-sizing: border-box; margin: 0; padding: 0; }
  html, body { width: 1200px; height: 930px; overflow: hidden; }
  body {
    background: var(--backdrop);
    position: relative;
    font-family: "Roboto", Arial, sans-serif;
  }
  .card {
    position: absolute;
    width: 560px;
    height: 320px;
    border-radius: 26px;
    overflow: hidden;
    box-shadow: 0 10px 24px rgba(0,0,0,0.25);
  }
  .card-front {
    left: 70px; top: 80px;
    background: var(--brand-green);
    color: var(--paper);
  }
  .card-back {
    left: 570px; top: 520px;
    background: var(--paper);
  }

  .brand-name {
    display: flex;
    align-items: center;
    gap: 10px;
    font-family: "Montserrat", Arial, sans-serif;
    font-weight: 700;
    white-space: nowrap;
  }
  .brand-square { flex: none; display: block; }

  .card-front .brand-name {
    position: absolute;
    left: 0; right: 0; top: 138px;
    justify-content: center;
    font-size: 30px;
    color: var(--paper);
  }
  .card-front .brand-square { width: 18px; height: 18px; background: var(--paper); }

  .front-web {
    position: absolute;
    left: 0; right: 0; bottom: 36px;
    text-align: center;
    font-size: 12px;
    letter-spacing: 0.3px;
  }

  .card-back .brand-name {
    position: absolute;
    left: 34px; top: 116px;
    font-size: 18px;
    color: var(--brand-green);
  }
  .card-back .brand-square { width: 12px; height: 12px; background: var(--brand-green); }

  .divider {
    position: absolute;
    left: 280px; top: 78px;
    width: 2px; height: 100px;
    background: var(--brand-green);
  }
  .contact-block {
    position: absolute;
    left: 298px; top: 72px;
  }
  .person-name {
    font-family: "Montserrat", Arial, sans-serif;
    font-weight: 700;
    font-size: 20px;
    color: var(--brand-green);
  }
  .person-role {
    font-size: 12px;
    color: var(--ink-grey);
    margin: 2px 0 10px;
  }
  .contact-list { list-style: none; }
  .contact-list li {
    display: flex;
    align-items: center;
    gap: 8px;
    font-size: 12.5px;
    color: var(--ink-grey);
    line-height: 17px;
    white-space: nowrap;
  }
  .contact-list svg { width: 10px; height: 10px; flex: none; }

  .footer-rule {
    position: absolute;
    left: 0; right: 0; bottom: 34px;
    height: 3px;
    background: var(--rule-grey);
  }
  .footer-band {
    position: absolute;
    left: 0; right: 0; bottom: 0;
    height: 26px;
    background: var(--brand-green);
  }
</style>
</head>
<body>
  <section class="card card-front" aria-label="Business card front">
    <h1 class="brand-name"><span class="brand-square"></span>Quillmark Homesteads</h1>
    <p class="front-web">www.quillmarkhomesteads.co.nz</p>
  </section>

  <section class="card card-back" aria-label="Business card back">
    <h2 class="brand-name"><span class="brand-square"></span>Quillmark Homesteads</h2>

    <div class="divider"></div>

    <div class="contact-block">
      <p class="person-name">Derek Tolvane</p>
      <p class="person-role">Founder</p>
      <ul class="contact-list">
        <li>
          <svg viewBox="0 0 10 10" aria-hidden="true"><path d="M2 1 L3.5 1 L4 3 L3 3.8 C3.6 5 4.8 6.3 6.2 7 L7 6 L9 6.5 L9 8 C9 8.6 8.5 9 8 9 C4.5 8.8 1.2 5.5 1 2 C1 1.4 1.4 1 2 1 Z" fill="var(--brand-green)"/></svg>
          0217394062
        </li>
        <li>
          <svg viewBox="0 0 10 10" aria-hidden="true"><rect x="0.8" y="2" width="8.4" height="6" fill="none" stroke="var(--brand-green)" stroke-width="1"/><path d="M1 2.3 L5 5.5 L9 2.3" fill="none" stroke="var(--brand-green)" stroke-width="1"/></svg>
          dtolvane@quillmarkhomesteads.co.nz
        </li>
        <li>
          <svg viewBox="0 0 10 10" aria-hidden="true"><circle cx="5" cy="5" r="4" fill="none" stroke="var(--brand-green)" stroke-width="1"/><path d="M1 5 H9 M5 1 C3 3.5 3 6.5 5 9 M5 1 C7 3.5 7 6.5 5 9" fill="none" stroke="var(--brand-green)" stroke-width="0.8"/></svg>
          www.quillmarkhomesteads.co.nz
        </li>
      </ul>
    </div>

    <div class="footer-rule"></div>
    <div class="footer-band"></div>
  </section>
</body>
</html>
```